The Quiet Harvest Book Cover

Cover for Multiauthor Ebook & Paper Print Book Cover

Book Title:
The Quiet Harvest: Lessons of Insight From A Circle of Mentors to Guide You Toward a Fuller Journey

This book will offer the wisdom and philosophies of a variety of different coaches to allow future clients to get a taste of you and your style and prepare them to work with you!

A coach does not fix you. Or heal you. They coach you - offer thoughts to ponder, guidance, techniques to try. All to help you plays and succeed at the game of life.

Each coach has their own personality, training, experience, method and philosophy they bring to the table. The underlying purpose is to guide you through the quiet harvest, to become the person you desire and aspire to be. Different coaches for different folks, yet they all have their own unique wisdom and special sauce to share.

This book is a collection of just that. A tasting of the wisdom and philosophies of a variety of different coaches for you to experience.

Types of Coaches: Clarity, Dreams, Goals, Motivation, Mindset,  Subconscious, Beliefs, Behavior, Accountability, Life, Wellness, Love & Dating, Relationships, Sex, Business, Career,  Executive,  Personal Development,  Writing, Wellness, Fitness, Parenting,  Style, Spirituality, Public Speaking, Financial,  Time management, Weight Loss, Running, Self esteem,  Tarot, Astrology, Enneagram, Soul path/ Dharma, Skills, Performance,  Speaking / Communication, Leadership, Shadow Work, Acting, Sports, ANY & ALL

Target Market(s)

Males or females looking for guidance and words of wisdom from an expert coach - maybe to find one that resonates with them to work with further. Ages 16 and up. Any Gender. International. Looking to improve their life!

Industry/Entity Type

Self Development, Wellness, Coaching, Personal Growth, Fitness, Spirituality, Business, Relationships

Font styles to use
Serif
Script

Colors
0054AA
0677BA
7BADD7
CADEEF
E8F1F8
FFF300
FFF600
FEFA6F
FFFEC7
FFFEE8

Requirements
Must have
• I am looking for a visually appealing, unique cover that encompasses the breadth and depth of the transformation that people can go through and inspires them to want to grow and change even more. I love when elegant and classic simplicity is combined with some kind of twist that catches the eye and provokes thought. I love complimentary fonts, colors, design elements. You can visit my Brindlemart Author Page - Dr. Marisol Pendergast Voyle to see my titles to see what I have liked! But I am also excited to see where you can make my vision even better!!
Nice to have
• Front Cover - Image, Title and Subtitle, The Lantern Publishing House, Spine - Title and Publishing House Logo, Back - Book Blurb, Authors Names, Info about Publishing House, ISBN Barcode
Should not have
• Anything too feminine or too masculine as I want to encourage coaches of all genders to participate.

```html
<!DOCTYPE html>
<html lang="en">
<head>
<meta charset="utf-8">
<title>The Quiet Harvest — Book Cover</title>
<link href="https://fonts.googleapis.com/css2?family=Allison&family=Cinzel:wght@400;600;700&family=Cormorant+SC:wght@500&family=Roboto:wght@400;500&family=Roboto+Condensed:wght@400&display=swap" rel="stylesheet">
<style>
  :root {
    --stage: #e9e9ea;
    --cover-grey: #a4a4a5;
    --cover-grey-light: #b9b9ba;
    --ink: #141414;
    --white: #ffffff;
    --band: #050505;
    --author-blue: #2a3f7a;
    --wing-deep: #0c1640;
    --wing-bright: #1aa6d6;
  }
  * { box-sizing: border-box; margin: 0; padding: 0; }
  html, body { width: 1200px; height: 849px; overflow: hidden; background: var(--stage); }
  .wrap {
    position: absolute; left: 90px; top: 75px; width: 1020px; height: 700px;
    display: flex; box-shadow: 0 18px 40px rgba(0,0,0,.18);
  }

  /* Back cover */
  .back { position: relative; width: 470px; height: 100%; background: linear-gradient(180deg, var(--cover-grey-light), var(--cover-grey)); }
  .back-body { position: absolute; left: 0; right: 0; top: 0; height: 515px; padding: 34px 40px 0; color: var(--white); }
  .back-title { font-family: "Cinzel", serif; font-weight: 600; font-size: 27px; line-height: 1.25; color: var(--ink); letter-spacing: .5px; transform: scaleX(.82); transform-origin: left; white-space: nowrap; }
  .back-subtitle { font-family: "Cormorant SC", serif; font-size: 11px; color: var(--ink); line-height: 1.15; margin-top: 2px; width: 300px; }
  .blurb { font-family: "Roboto", sans-serif; font-size: 11px; line-height: 1.5; margin-top: 16px; text-align: justify; }
  .blurb p + p { margin-top: 9px; }
  .authors-label { font-family: "Roboto", sans-serif; font-size: 11px; line-height: 14px; color: var(--author-blue); margin: 18px 0 0 110px; }
  .authors { display: grid; grid-template-columns: 1fr 1fr; column-gap: 40px; margin: 12px 0 0 30px; width: 300px; list-style: none; }
  .authors li { font-family: "Roboto", sans-serif; font-size: 11px; line-height: 15px; color: var(--author-blue); }
  .publisher-band { position: absolute; left: 0; right: 0; bottom: 0; height: 180px; background: var(--band); color: var(--white); padding: 16px 40px; }
  .publisher-band h3 { font-family: "Roboto Condensed", sans-serif; font-weight: 400; font-size: 12px; text-align: center; margin-bottom: 6px; }
  .publisher-band p { font-family: "Roboto", sans-serif; font-size: 11.5px; line-height: 1.65; text-align: justify; }

  /* Spine */
  .spine { position: relative; width: 70px; height: 100%; background: var(--cover-grey-light); border-left: 1px solid rgba(0,0,0,.08); border-right: 1px solid rgba(0,0,0,.12); }
  .spine-title { position: absolute; top: 40px; left: 0; width: 70px; height: 470px; writing-mode: vertical-rl; display: flex; align-items: center; justify-content: flex-start; gap: 6px; }
  .spine-script { font-family: "Allison", cursive; font-size: 58px; color: var(--white); line-height: 1; }
  .spine-serif { font-family: "Cinzel", serif; font-weight: 700; font-style: italic; font-size: 26px; color: var(--ink); letter-spacing: 1px; }
  .spine-band { position: absolute; left: 0; right: 0; bottom: 0; height: 180px; background: var(--band); display: flex; flex-direction: column; align-items: center; padding-top: 10px; gap: 8px; }
  .spine-band .pub-name { writing-mode: vertical-rl; font-family: "Roboto", sans-serif; font-size: 8.5px; color: var(--white); white-space: nowrap; }
  .spine-band .pub-dot { width: 11px; height: 11px; border-radius: 50%; background: var(--white); flex: none; }

  /* Front cover */
  .front { position: relative; width: 480px; height: 100%; background: linear-gradient(180deg, var(--cover-grey-light), var(--cover-grey)); }
  .title-block { position: absolute; left: 0; right: 0; top: 60px; height: 200px; }
  .title-the { position: absolute; left: 55px; top: -10px; font-family: "Allison", cursive; font-size: 110px; color: var(--white); line-height: 1; }
  .title-main { position: absolute; left: 0; right: 0; top: 70px; text-align: center; font-family: "Cinzel", serif; font-weight: 700; font-size: 58px; color: var(--ink); letter-spacing: 2px; text-shadow: 1px 1px 0 var(--white); }
  .title-harvest { position: absolute; left: 150px; top: 110px; font-family: "Allison", cursive; font-size: 120px; color: var(--white); line-height: 1; }
  .title-flourish { position: absolute; left: 0; top: 0; width: 480px; height: 200px; }
  .cover-image { position: absolute; left: 130px; top: 300px; width: 220px; height: 210px; }
  .subtitle { position: absolute; left: 60px; right: 60px; top: 555px; text-align: center; font-family: "Cormorant SC", serif; font-size: 16px; line-height: 1.05; color: var(--white); letter-spacing: .5px; }
  .imprint { position: absolute; left: 0; right: 0; bottom: 30px; display: flex; flex-direction: column; align-items: center; gap: 8px; }
  .imprint .pub-dot { width: 20px; height: 20px; border-radius: 50%; background: var(--ink); }
  .imprint .pub-name { font-family: "Roboto", sans-serif; font-size: 14px; color: var(--ink); }
</style>
</head>
<body>
<div class="wrap">

  <section class="back">
    <div class="back-body">
      <h2 class="back-title">THE QUIET HARVEST</h2>
      <p class="back-subtitle">Lessons of Insight From A Circle of Mentors to Guide You Toward a Fuller Journey</p>
      <div class="blurb">
        <p>A coach does not fix you. Or heal you. They coach you - by offering thoughts to ponder, guidance, techniques to try - All to help you play and succeed at the game of life.</p>
        <p>Each coach has their own personality, training, experience, method and philosophy they bring to the table. The underlying purpose is to guide you through the quiet harvest, to become the person you desire and aspire to be. Different coaches for different folks, yet they all have their own unique wisdom and special sauce to share.</p>
        <p>This book is a collection of just that. A tasting of the wisdom and philosophies of a variety of different coaches for you to experience.</p>
      </div>
      <p class="authors-label">Authors names</p>
      <ul class="authors">
        <li>Author name</li><li>Author name</li>
        <li>Author name</li><li>Author name</li>
        <li>Author name</li><li>Author name</li>
        <li>Author name</li><li>Author name</li>
        <li>Author name</li><li>Author name</li>
        <li>Author name</li><li>Author name</li>
        <li>Author name</li><li>Author name</li>
        <li>Author name</li><li>Author name</li>
        <li>Author name</li><li>Author name</li>
        <li>Author name</li><li>Author name</li>
      </ul>
    </div>
    <div class="publisher-band">
      <h3>About the Publisher</h3>
      <p>The Lantern Publishing House is the publishing arm of The Lantern to Wellness, a company founded and led by Dr. Marisol Voyle DPT in order to educate, inspire, and empower healing and love for oneself and for others. The Lantern Publishing House seeks to unlock the potential of each individual to amplify their voice and help improve our human experience. Please visit lanterntowellness.net to learn about future publications.</p>
    </div>
  </section>

  <section class="spine">
    <div class="spine-title">
      <span class="spine-script">the</span>
      <span class="spine-serif">QUIET HARVEST</span>
    </div>
    <div class="spine-band">
      <span class="pub-dot"></span>
      <span class="pub-name">THE LANTERN PUBLISHING HOUSE</span>
    </div>
  </section>

  <section class="front">
    <div class="title-block">
      <svg class="title-flourish" viewBox="0 0 480 200" aria-hidden="true">
        <path d="M0 82 C40 80 60 78 80 70" fill="none" stroke="#ffffff" stroke-width="1.2"/>
        <path d="M300 178 C360 170 420 150 480 150" fill="none" stroke="#ffffff" stroke-width="1.2"/>
      </svg>
      <span class="title-the">the</span>
      <h1 class="title-main">QUIET</h1>
      <span class="title-harvest">harvest</span>
    </div>
    <svg class="cover-image" viewBox="0 0 220 210" role="img" aria-label="Dark blue butterfly with bright turquoise wing markings">
      <defs>
        <radialGradient id="wing" cx="50%" cy="75%" r="70%">
          <stop offset="0" stop-color="#1aa6d6"/>
          <stop offset="1" stop-color="#0c1640"/>
        </radialGradient>
      </defs>
      <ellipse cx="110" cy="125" rx="108" ry="80" fill="url(#wing)"/>
    </svg>
    <p class="subtitle">LESSONS OF INSIGHT FROM A CIRCLE<br>OF MENTORS TO GUIDE YOU TOWARD<br>A FULLER JOURNEY</p>
    <div class="imprint">
      <span class="pub-dot"></span>
      <span class="pub-name">The Lantern Publishing House</span>
    </div>
  </section>

</div>
</body>
</html>
```